New Company Business Card design

Looking for a corporate looking business card utilising my new logo design - the logo i would like embossed as one option and flat as another - simplistic but stylish - less is more - we are an import export business launching into the market - i would like a couple of options as main background - Grey or Black

```html
<!DOCTYPE html>
<html lang="en">
<head>
<meta charset="utf-8">
<title>Meridian Trade Partners – Business Card</title>
<link href="https://fonts.googleapis.com/css2?family=Cinzel:wght@600&family=Open+Sans:wght@400;700&display=swap" rel="stylesheet">
<style>
  :root {
    --page-bg: #e9e6e1;
    --card-white: #fbfbfa;
    --brand-blue: #1a78c2;
    --brand-grey: #7d7f82;
    --card-black: #26282b;
    --text-white: #ffffff;
  }
  * { margin: 0; padding: 0; box-sizing: border-box; }
  html, body {
    width: 1200px; height: 848px; overflow: hidden;
    background: var(--page-bg);
  }
  .canvas {
    position: relative; width: 1200px; height: 848px;
  }
  .card {
    position: absolute; left: 290px;
    width: 620px; height: 354px;
    overflow: hidden;
    border-radius: 4px;
  }
  .card--front { top: 46px; background: var(--card-white); }
  .card--back { top: 448px; background: var(--card-black); }

  /* Front */
  .front-brand {
    position: absolute; inset: 0;
    display: flex; flex-direction: column; align-items: center; justify-content: center;
  }
  .brand-row { display: flex; align-items: center; gap: 14px; }
  .brand-dot {
    width: 30px; height: 30px; border-radius: 50%;
    background: var(--brand-blue);
  }
  .brand-name {
    font-family: "Cinzel", Georgia, serif; font-weight: 600;
    color: var(--brand-blue); font-size: 34px; letter-spacing: 1px;
    line-height: 1;
  }
  .brand-rule {
    width: 380px; height: 2px; background: var(--brand-grey);
    margin: 12px 0 8px;
  }
  .brand-tagline {
    font-family: "Cinzel", Georgia, serif; font-weight: 600;
    color: var(--brand-grey); font-size: 13px; letter-spacing: 1.6px;
  }

  /* Back */
  .back-panel { position: absolute; inset: 0; }
  .contact {
    position: absolute; left: 40px; top: 96px;
    font-family: "Open Sans", Arial, sans-serif; color: var(--text-white);
  }
  .contact-name { font-weight: 700; font-size: 22px; letter-spacing: 0.5px; }
  .contact-role { font-size: 14px; margin-top: 2px; }
  .contact-address { font-size: 14px; line-height: 1.35; margin-top: 14px; }
  .contact-list { list-style: none; margin-top: 12px; font-size: 14px; }
  .contact-list li { display: flex; align-items: center; gap: 12px; height: 21px; }
  .contact-list svg { width: 14px; height: 14px; fill: var(--text-white); flex: none; }
  .back-brand {
    position: absolute; left: 370px; top: 140px; width: 240px;
    display: flex; flex-direction: column; align-items: center;
  }
  .back-brand .brand-row { gap: 8px; }
  .back-brand .brand-dot { width: 16px; height: 16px; }
  .back-brand .brand-name { font-size: 19px; letter-spacing: 0.5px; }
  .back-brand .brand-rule { width: 220px; height: 1px; margin: 7px 0 5px; }
  .back-brand .brand-tagline { font-size: 8px; letter-spacing: 1px; }
</style>
</head>
<body>
<main class="canvas">

  <section class="card card--front" aria-label="Card front">
    <div class="front-brand">
      <div class="brand-row">
        <span class="brand-dot"></span>
        <span class="brand-name">MERIDIAN TRADE PARTNERS</span>
      </div>
      <div class="brand-rule"></div>
      <p class="brand-tagline">WORLDWIDE SUPPLY FOR NEARBY DEMAND</p>
    </div>
  </section>

  <section class="card card--back" aria-label="Card back">
    <svg class="back-panel" viewBox="0 0 620 354" preserveAspectRatio="none" aria-hidden="true">
      <polygon points="0,0 400,0 290,354 0,354" fill="var(--brand-blue)"/>
      <polygon points="400,0 416,0 306,354 290,354" fill="var(--brand-grey)"/>
    </svg>

    <div class="contact">
      <p class="contact-name">DANIEL MARSH</p>
      <p class="contact-role">CEO/FOUNDER</p>
      <p class="contact-address">412 Harbor View Road<br>Juneau, Alaska 99801</p>
      <ul class="contact-list">
        <li><svg viewBox="0 0 24 24"><path d="M6.6 10.8a15 15 0 0 0 6.6 6.6l2.2-2.2a1 1 0 0 1 1-.25 11.4 11.4 0 0 0 3.6.57 1 1 0 0 1 1 1V20a1 1 0 0 1-1 1A17 17 0 0 1 3 4a1 1 0 0 1 1-1h3.5a1 1 0 0 1 1 1c0 1.25.2 2.45.57 3.57a1 1 0 0 1-.25 1z"/></svg>555 310 2284</li>
        <li><svg viewBox="0 0 24 24"><path d="M7 1h10a2 2 0 0 1 2 2v18a2 2 0 0 1-2 2H7a2 2 0 0 1-2-2V3a2 2 0 0 1 2-2zm0 3v14h10V4zm5 15.5a1.2 1.2 0 1 0 0 2.4 1.2 1.2 0 0 0 0-2.4z"/></svg>555 472 8196</li>
        <li><svg viewBox="0 0 24 24"><path d="M6 2h12v6H6zM4 9h16a2 2 0 0 1 2 2v7h-4v4H6v-4H2v-7a2 2 0 0 1 2-2zm4 7v4h8v-4z"/></svg>555 624 0375</li>
        <li><svg viewBox="0 0 24 24"><path d="M2 5h20v14H2zm2 2v.5l8 5.5 8-5.5V7l-8 5.5z"/></svg>daniel@meridiantrade.com</li>
        <li><svg viewBox="0 0 24 24"><path d="M12 2a10 10 0 1 0 0 20 10 10 0 0 0 0-20zm0 2c1.1 1.4 1.9 3.4 2.2 7H9.8c.3-3.6 1.1-5.6 2.2-7zm-2.2 9h4.4c-.3 3.6-1.1 5.6-2.2 7-1.1-1.4-1.9-3.4-2.2-7z"/></svg>www.meridiantrade.com</li>
      </ul>
    </div>

    <div class="back-brand">
      <div class="brand-row">
        <span class="brand-dot"></span>
        <span class="brand-name">MERIDIAN TRADE PARTNERS</span>
      </div>
      <div class="brand-rule"></div>
      <p class="brand-tagline">WORLDWIDE SUPPLY FOR NEARBY DEMAND</p>
    </div>
  </section>

</main>
</body>
</html>
```